Stationary Suite for Aussie Law Firm

We are a small law firm operating out of Albany, Western Australia. We have a logo, which we love and was the winner of a ArtworkHive contest last year.
We require a suite of business stationary products incorporating our logo and contact details. These should be:
1. Letterhead (A4)
The letterhead should incorporate the following information in addition to the logo:
ABN 38 602 917 255 (this is our Australian Business Number)
Beatrix Lund atf The BJL Legal Trust t/as Harbour Gate Legal & Conveyancing (legal name of the business)
Address: Wexley House, Wexley Street, Albany
Postal Address: PO Box 8147, Albany WA 6332
Telephone: 0491 670 382
Facsimile: 08 9722 5913
Email: info@harbourgatelegal.com.au
Website: www.harbourgatelegal.com.au
2. Business Card (90mm x 55mm)
I've attached my current business card layout just for your information.
The front of the business card should include the following information in addition to the logo:
Beatrix Lund
Director & Principal Solicitor
Telephone: 0491 670 382
Facsimile: 08 9722 5913
Email: beatrix@harbourgatelegal.com.au
The back of the card should be similar to the back of my existing card, but should only have the logo in white and the address of our website (www.harbourgatelegal.com.au)
3. Email signature block
This should include the same information as the front of the business card.
4. With Compliments slip (DL size)
The With Compliments slip should include the same information as the Letterhead.
5. Banner (830mm x 2000mm)
We need a banner designed for use at marketing events. This should include our website details and logo - other than that you have fairly free reign with the design.
6. Flyer (DL)
We need a flyer setting out our services and main contact details for use at marketing events. The details to be included are:
Telephone: 0491 670 382
Web: www.harbourgatelegal.com.au
Areas of law:
Wills & Estate Planning
Probate & Letters of Administration
Property Law & Conveyancing
General Commercial Law
Business Law
Style guide:
Please look at our website for an idea as to the style of designs we are looking for - www.harbourgatelegal.com.au. The design should be modern, sharp and professional.
Colours:
The CMYK details for the colours in our logo are:
Light Blue C72 M5 Y0 K0
Dark Blue C97 M72 Y16 K30
Edit 31/7/2014
I have added a couple of photos that we have used on our website, and additional photos. These are from our local area, so feel free to use these in your designs or to inform them.
- Calibri, Century Gothic

```html
<!DOCTYPE html>
<html lang="en">
<head>
<meta charset="utf-8">
<title>Harbour Gate Legal &amp; Conveyancing – Event Banner</title>
<link href="https://fonts.googleapis.com/css2?family=Lato:wght@400;700&display=swap" rel="stylesheet">
<style>
  :root {
    --navy: #27386e;
    --sky: #3aa6d8;
    --teal: #2f8fb3;
    --teal-deep: #1f6f8f;
    --sea-light: #8fbfd0;
    --grey-swoosh: #d9dbde;
    --white: #ffffff;
    --stage: #d6d6d6;
  }
  * { box-sizing: border-box; margin: 0; padding: 0; }
  html, body {
    width: 1200px; height: 1067px; overflow: hidden;
    background: var(--stage);
    font-family: "Lato", sans-serif;
  }
  .banner {
    position: absolute; left: 390px; top: 34px;
    width: 420px; height: 1000px;
    background: var(--white);
    overflow: hidden;
  }
  .banner__header {
    position: absolute; left: 0; top: 0; width: 100%; height: 320px;
  }
  .banner__header svg { position: absolute; inset: 0; }
  .brand-name {
    position: absolute; left: 0; right: 0; top: 112px;
    text-align: center; color: var(--navy);
    font-weight: 400; font-size: 27px; line-height: 1.15; letter-spacing: 0.5px;
  }
  .services { position: absolute; left: 0; top: 314px; width: 100%; list-style: none; }
  .service {
    height: 53px; display: flex; align-items: center; justify-content: center;
    font-weight: 700; font-size: 21px;
  }
  .service--light { background: var(--white); color: var(--navy); }
  .service--dark { background: var(--teal); color: var(--white); }
  .service--sea { background: linear-gradient(90deg, var(--teal-deep), var(--sea-light) 60%, var(--teal-deep)); color: var(--white); }
  .photo {
    position: absolute; left: 0; top: 579px; width: 100%; height: 421px;
    background: linear-gradient(180deg, #3f7f92 0%, #6fa5b4 35%, #a9c7cf 70%, #c9d6d6 100%);
  }
  .photo__shade {
    position: absolute; left: 0; top: 579px; width: 100%; height: 70px;
  }
  .web-band {
    position: absolute; left: 0; top: 890px; width: 100%; height: 46px;
    background: rgba(47,143,179,0.88);
    display: flex; align-items: center; justify-content: center;
    color: var(--white); font-weight: 700; font-size: 19px; letter-spacing: 1px;
  }
</style>
</head>
<body>
  <div class="banner">
    <div class="banner__header">
      <svg width="420" height="320" viewBox="0 0 420 320" aria-hidden="true">
        <rect x="0" y="200" width="420" height="120" fill="var(--teal)"/>
        <path d="M0 200 Q210 290 420 200 L420 222 Q210 270 0 222 Z" fill="var(--grey-swoosh)"/>
        <path d="M0 0 H420 V200 Q210 300 0 200 Z" fill="var(--white)"/>
        <path d="M0 170 Q210 250 420 170 L420 200 Q210 270 0 200 Z" fill="var(--grey-swoosh)"/>
        <path d="M0 222 Q210 275 420 222 L420 240 Q210 285 0 240 Z" fill="#3d9cc0" opacity="0.6"/>
      </svg>
      <p class="brand-name">Harbour Gate<br>Legal &amp; Conveyancing</p>
    </div>

    <ul class="services">
      <li class="service service--light">Wills &amp; Estate Planning</li>
      <li class="service service--dark">Probate &amp; Letters of Administration</li>
      <li class="service service--light">Property Law &amp; Conveyancing</li>
      <li class="service service--sea">General Commercial Law</li>
      <li class="service service--light">Business Law</li>
    </ul>

    <div class="photo" role="img" aria-label="Photograph of a person walking along a long wooden jetty over the sea"></div>
    <svg class="photo__shade" width="420" height="70" viewBox="0 0 420 70" aria-hidden="true">
      <path d="M0 0 H420 V20 Q210 100 0 20 Z" fill="var(--teal-deep)" opacity="0.75"/>
    </svg>

    <div class="web-band">WWW.HARBOURGATELEGAL.COM.AU</div>
  </div>
</body>
</html>
```